****Business Card Design for Quarrystone Development. Design based around attached logo/company name

I’m looking for business card design for my company Quarrystone Development Group,LLC. Design should be professional, sharp and minimal. Outside of the attached logos, greyscale colors for remainder of cards. My thoughts are two-sided card with attached logo on one side and my info on the other but open to one-sided as well with right design.
Target Market(s)
Real estate professionals including banks, private investors, property owners, developers, commercial tenants like Brewlantern, Grovika or Tanquist’s.
Industry/Entity Type
Commercial real estate development and investments.
Contact Information for Business Card
Name, title, email, phone #’s, web address and physical address
Font styles to use
Other font styles liked:
- Helvetica, Garamond, etc
Colors
Designer to choose only greyscale colors for use in the design.
Requirements
Must have
- Attached logo first or second options.
Nice to have
- Two sided card with logo on one side. Attached Logo/company name can be laid out any way that flows as long as it’s legible.name
Should not have
- No loud colors. ***Please do not include logo, I have removed the company design with a logo image.

```html
<!DOCTYPE html>
<html lang="en">
<head>
<meta charset="utf-8">
<title>Quarrystone Development Group, LLC — Business Card</title>
<link rel="stylesheet" href="https://fonts.googleapis.com/css2?family=Cinzel:wght@400;700&family=Arimo:wght@400&display=swap">
<style>
  :root {
    --backdrop: #d8d8d5;
    --card: #5a6475;
    --ink-light: #eef0f3;
    --ink-soft: #c9ced6;
    --ink-muted: #8a93a1;
    --rule: #9aa0a8;
    --ink-deep: #434b58;
  }
  * { box-sizing: border-box; margin: 0; padding: 0; }
  html, body { width: 1200px; height: 801px; overflow: hidden; }
  body {
    background: var(--backdrop);
    display: flex;
    align-items: center;
    justify-content: center;
    gap: 60px;
    font-family: "Arimo", Helvetica, Arial, sans-serif;
  }
  .card {
    position: relative;
    width: 520px;
    height: 297px;
    background: var(--card);
    box-shadow: 0 6px 18px rgba(0,0,0,0.18);
  }

  /* info side */
  .wordmark {
    position: absolute;
    top: 32px;
    right: 34px;
    text-align: right;
    font-family: "Cinzel", "Times New Roman", serif;
    font-weight: 400;
    line-height: 1.1;
  }
  .wordmark .name-main {
    font-size: 30px;
    letter-spacing: 2px;
    display: block;
    color: var(--ink-light);
    padding-bottom: 2px;
    border-bottom: 1px solid var(--ink-muted);
  }
  .wordmark .name-sub {
    font-size: 11px;
    letter-spacing: 1.6px;
    display: block;
    margin-top: 3px;
    color: var(--ink-muted);
  }
  .divider {
    position: absolute;
    left: 40px;
    right: 22px;
    top: 160px;
    height: 1px;
    background: var(--rule);
  }
  .person {
    position: absolute;
    left: 40px;
    top: 118px;
    color: var(--ink-light);
  }
  .person .full-name {
    font-family: "Cinzel", "Times New Roman", serif;
    font-weight: 700;
    font-size: 15px;
    letter-spacing: 1px;
    display: block;
  }
  .person .role { font-size: 13px; color: var(--ink-soft); display: block; margin-top: 1px; }
  .contacts {
    position: absolute;
    left: 40px;
    top: 178px;
    list-style: none;
    color: var(--ink-light);
    font-size: 12.5px;
    line-height: 1.55;
  }
  .contacts li { display: flex; align-items: center; gap: 7px; }
  .contacts svg { width: 10px; height: 10px; fill: var(--ink-soft); flex: none; }
  .address {
    position: absolute;
    right: 34px;
    top: 178px;
    text-align: right;
    font-style: normal;
    color: var(--ink-light);
    font-size: 12.5px;
    line-height: 1.55;
  }

  /* logo side */
  .brand {
    position: absolute;
    inset: 0;
    display: flex;
    flex-direction: column;
    align-items: center;
    justify-content: center;
    font-family: "Cinzel", "Times New Roman", serif;
    font-weight: 400;
    color: var(--ink-deep);
    line-height: 1.15;
    text-align: center;
  }
  .brand .name-main {
    font-size: 40px;
    letter-spacing: 2px;
    padding-bottom: 2px;
    border-bottom: 1px solid var(--ink-deep);
  }
  .brand .name-sub { font-size: 15px; letter-spacing: 2px; margin-top: 4px; }
</style>
</head>
<body>
  <section class="card card-info" aria-label="Contact side">
    <div class="wordmark">
      <span class="name-main">QUARRYSTONE</span>
      <span class="name-sub">DEVELOPMENT GROUP, LLC</span>
    </div>
    <div class="person">
      <span class="full-name">DORIAN VALE</span>
      <span class="role">Founder/CEO</span>
    </div>
    <div class="divider"></div>
    <ul class="contacts">
      <li><svg viewBox="0 0 10 10"><path d="M2 0.5 L3.6 2.4 L2.8 3.6 Q4 6 6.4 7.2 L7.6 6.4 L9.5 8 L8 9.6 Q2.5 8.5 0.4 2 Z"/></svg>(123)-555-0184</li>
      <li><svg viewBox="0 0 10 10"><path d="M0.5 2 H9.5 V8.5 H0.5 Z M0.5 2 L5 5.5 L9.5 2"/></svg>info@quarrystonedevelopment.com</li>
      <li><svg viewBox="0 0 10 10"><circle cx="5" cy="5" r="4.5"/></svg>www.quarrystonedevelopment.com</li>
    </ul>
    <address class="address">
      2150 Ledgerstone Avenue<br>
      Harrow Point HP 3062
    </address>
  </section>

  <section class="card card-brand" aria-label="Logo side">
    <div class="brand">
      <span class="name-main">QUARRYSTONE</span>
      <span class="name-sub">DEVELOPMENT GROUP, LLC</span>
    </div>
  </section>
</body>
</html>
```